New Business Card Design Project

Use the flyer uploaded and website www.brightoakbuilders.com for inspiration.
List Our Services on Backside of business cards
Marcus Delling
Harborline Builders Inc.
Licensed General Contractors
858-471-6093

Contact Information for Business Card

Use the flyer uploaded and website www.brightoakbuilders.com for inspiration. List Our Services on Backside of business cards Marcus Delling Harborline Builders Inc. Licensed General Contractors 858-471-6093

```html
<!DOCTYPE html>
<html lang="en">
<head>
<meta charset="utf-8">
<title>Harborline Builders – Business Card</title>
<link href="https://fonts.googleapis.com/css2?family=Cormorant+Garamond:wght@400;500&family=Arimo:wght@400&display=swap" rel="stylesheet">
<style>
  :root {
    --backdrop: #d9d9db;
    --card-dark: #333335;
    --card-light: #ffffff;
    --ink-light: #f2f2f2;
    --ink-dark: #2b2b2b;
    --ink-muted: #555555;
  }
  * { box-sizing: border-box; margin: 0; padding: 0; }
  html, body {
    width: 1200px; height: 800px; overflow: hidden;
    background: var(--backdrop);
  }
  .sheet {
    width: 1200px; height: 800px;
    display: flex; align-items: center; justify-content: center; gap: 48px;
  }
  .card {
    width: 525px; height: 300px;
    border-radius: 22px;
    position: relative;
    box-shadow: 0 10px 24px rgba(0,0,0,0.18);
  }
  /* Front: contact side */
  .card--front { background: var(--card-dark); color: var(--ink-light); }
  .contact {
    position: absolute; left: 40px; bottom: 48px;
  }
  .contact__name {
    font-family: "Cormorant Garamond", serif;
    font-weight: 400; font-size: 26px; letter-spacing: 2px;
    text-transform: uppercase; margin-bottom: 14px;
  }
  .contact__list { list-style: none; font-family: "Arimo", sans-serif; font-size: 15px; line-height: 1.45; }
  .contact__item { display: flex; align-items: center; gap: 9px; }
  .contact__icon { width: 12px; height: 12px; fill: var(--ink-light); flex: none; }
  .contact__company { font-family: "Arimo", sans-serif; font-size: 15px; line-height: 1.45; margin-top: 2px; }

  /* Back: services side */
  .card--back { background: var(--card-light); color: var(--ink-dark); }
  .services {
    position: absolute; left: 36px; top: 40px;
    list-style: none; font-family: "Arimo", sans-serif; font-size: 15px; line-height: 1.7;
  }
  .services__item { display: flex; align-items: center; gap: 12px; }
  .services__item::before {
    content: ""; width: 7px; height: 7px; background: var(--ink-dark); flex: none;
  }
  .brand {
    position: absolute; right: 30px; top: 110px; width: 230px; text-align: center;
  }
  .brand__name {
    font-family: "Cormorant Garamond", serif; font-weight: 400;
    font-size: 27px; letter-spacing: 1px; text-transform: uppercase; color: var(--ink-dark);
  }
  .brand__web {
    font-family: "Cormorant Garamond", serif; font-weight: 400;
    font-size: 13px; letter-spacing: 2px; text-transform: uppercase; color: var(--ink-muted);
    margin-top: 18px;
  }
</style>
</head>
<body>
<main class="sheet">
  <section class="card card--front" aria-label="Business card front">
    <div class="contact">
      <h1 class="contact__name">Marcus Delling</h1>
      <ul class="contact__list">
        <li class="contact__item">
          <svg class="contact__icon" viewBox="0 0 12 12" aria-hidden="true"><path d="M2.4 0.6 4.2 2.6 3.2 4.1c.7 1.6 2 2.9 3.6 3.6l1.5-1 2 1.8-1 2.1C5 10.6 1.4 7 0.4 1.6z"/></svg>
          858-471-6093
        </li>
        <li class="contact__item">
          <svg class="contact__icon" viewBox="0 0 12 12" aria-hidden="true"><path d="M0 2h12v8H0z M1 3l5 3.6L11 3" fill="none" stroke="currentColor"/><path d="M0 2h12L6 6.5z"/></svg>
          info@brightoakbuilders.com
        </li>
        <li class="contact__item">
          <svg class="contact__icon" viewBox="0 0 12 12" aria-hidden="true"><circle cx="6" cy="6" r="5.5"/></svg>
          www.brightoakbuilders.com
        </li>
      </ul>
      <p class="contact__company">Harborline Builders Inc.<br>Licensed General Contractors</p>
    </div>
  </section>

  <section class="card card--back" aria-label="Business card back">
    <ul class="services">
      <li class="services__item">Kitchen &amp; Bath</li>
      <li class="services__item">Painting : Interior &amp; Exterior</li>
      <li class="services__item">Flooring : Carpet, Vinyl, Wood</li>
      <li class="services__item">Window &amp; Door Replacement</li>
      <li class="services__item">Plumbing : Repairs &amp; Upgrades</li>
      <li class="services__item">Energy- Efficient Upgrades</li>
      <li class="services__item">Deck &amp; Patio Construction</li>
      <li class="services__item">Water &amp; Mold Damage</li>
      <li class="services__item">Garage Renovation</li>
    </ul>
    <div class="brand">
      <p class="brand__name">Harborline Builders</p>
      <p class="brand__web">www.brightoakbuilders.com</p>
    </div>
  </section>
</main>
</body>
</html>
```